RWM Kids Choir

Card to hand out or mail out with our own mailing labels. Needs to be appealing to families with children ages 4 yrs through 6th grade, who have an interest in musical experiences for the kids in a contemporary Bible teaching/church setting. We have 3 different kids choirs: 4-yr-old & Kindergarten Choir, 1st-3rd grade choir, and 4th-6th grade choir. This is a FREE after-school program every Tuesday from 3:30-5:00. Transportation for grades 1-6 from local schools is provided. Parents should expect their children to experience fun, friends, music, recreation, games, snacks, character building, Bible teaching, in an encouraging church environment.

Industry/Entity Type

Church

Requirements
Nice to have
• Bight colors

```html
<!DOCTYPE html>
<html lang="en">
<head>
<meta charset="utf-8">
<title>RWM Kids Choir</title>
<link href="https://fonts.googleapis.com/css2?family=Arimo:wght@400;700&display=swap" rel="stylesheet">
<style>
  :root {
    --sun-yellow: #ffd21f;
    --sun-orange: #f5a21a;
    --sky-blue: #1f8fd0;
    --deep-blue: #0c5fa8;
    --light-blue: #4fb3e6;
    --choir-green: #2e9f3e;
    --choir-blue: #1c6fc0;
    --choir-red: #c81f25;
    --badge-red: #d2232a;
    --wine: #7a1418;
    --navy: #1b2a6b;
    --white: #ffffff;
    --photo-warm: #8a5a44;
    --photo-dark: #2b2330;
  }
  * { margin: 0; padding: 0; box-sizing: border-box; }
  html, body { width: 1200px; height: 930px; overflow: hidden; background: #ffffff; }
  .card {
    position: relative;
    width: 1200px;
    height: 930px;
    overflow: hidden;
    font-family: "Arimo", Arial, sans-serif;
    background: radial-gradient(ellipse at 30% 95%, var(--sun-yellow) 0%, var(--sun-orange) 70%);
  }
  .backdrop { position: absolute; inset: 0; }
  .ministry-seal {
    position: absolute;
    left: 78px; top: 342px;
    width: 234px; height: 234px;
    border-radius: 50%;
    background: var(--white);
    border: 6px solid #e9e9e9;
    display: flex; align-items: center; justify-content: center;
    text-align: center;
    color: var(--wine);
    font-weight: 700;
    font-size: 30px;
    line-height: 1.15;
    padding: 20px;
  }
  .free-badge {
    position: absolute;
    left: 339px; top: 393px;
    width: 168px; height: 168px;
    border-radius: 50%;
    background: var(--badge-red);
    border: 4px solid #f0c0c0;
    color: var(--white);
    display: flex; flex-direction: column; align-items: center; justify-content: center;
    text-align: center;
  }
  .free-badge .free { font-size: 36px; font-weight: 700; line-height: 1; }
  .free-badge .detail { font-size: 22px; font-weight: 700; line-height: 1.1; margin-top: 4px; }
  .choir-heading {
    position: absolute;
    left: 183px; top: 637px;
    width: 660px; height: 68px;
    border-radius: 12px;
    background: var(--white);
    box-shadow: 0 4px 8px rgba(0,0,0,.3);
    color: var(--wine);
    font-size: 48px; font-weight: 700;
    display: flex; align-items: center; justify-content: center;
  }
  .choir-list {
    position: absolute;
    left: 108px; top: 720px;
    display: flex; gap: 12px;
  }
  .choir {
    width: 268px; height: 165px;
    border-radius: 10px;
    border: 3px solid rgba(255,255,255,.6);
    box-shadow: 0 6px 10px rgba(0,0,0,.3);
    color: var(--white);
    font-size: 34px; font-weight: 700; line-height: 1.2;
    display: flex; align-items: center; justify-content: center;
    text-align: center;
    padding: 10px;
  }
  .choir--little { background: linear-gradient(var(--choir-green), #1f7d2c); }
  .choir--middle { background: linear-gradient(var(--choir-blue), #0f4f96); }
  .choir--older { background: linear-gradient(var(--choir-red), #9a1418); }
  .church-name {
    position: absolute;
    left: 955px; top: 705px;
    width: 220px;
    text-align: center;
    color: var(--navy);
    font-size: 32px; font-weight: 700; line-height: 1.15;
    letter-spacing: 2px;
    text-transform: uppercase;
  }
</style>
</head>
<body>
<main class="card">
  <svg class="backdrop" width="1200" height="930" viewBox="0 0 1200 930" aria-hidden="true">
    <polygon points="0,430 1200,410 1200,660 620,610 0,560" fill="var(--sky-blue)"/>
    <polygon points="600,540 1200,470 1200,660 620,610" fill="var(--deep-blue)" opacity=".55"/>
    <polygon points="0,560 110,650 0,870" fill="var(--light-blue)"/>
    <polygon points="0,0 260,0 0,40" fill="var(--sun-yellow)"/>
  </svg>
  <svg class="backdrop" width="1200" height="930" viewBox="0 0 1200 930" role="img" aria-label="Photo of children singing together in a choir">
    <defs>
      <linearGradient id="choirPhoto" x1="0" y1="0" x2="1" y2="1">
        <stop offset="0" stop-color="var(--photo-warm)"/>
        <stop offset=".5" stop-color="#b98a72"/>
        <stop offset="1" stop-color="var(--photo-dark)"/>
      </linearGradient>
    </defs>
    <polygon points="0,20 1200,0 1200,425 0,440" fill="url(#choirPhoto)"/>
    <polygon points="330,0 1200,0 1200,40 370,30" fill="var(--sky-blue)"/>
  </svg>

  <div class="ministry-seal">RWM Kids Choir</div>

  <div class="free-badge">
    <span class="free">FREE</span>
    <span class="detail">after-school<br>program</span>
  </div>

  <h1 class="choir-heading">3 different kids choirs</h1>

  <section class="choir-list">
    <div class="choir choir--little">4-yr-old &amp; Kindergarten Choir</div>
    <div class="choir choir--middle">1st-3rd grade choir</div>
    <div class="choir choir--older">4th-6th grade choir</div>
  </section>

  <div class="church-name">Grace Hill Church</div>
</main>
</body>
</html>
```